New Business Card Design for Manufacturing

We are an engineering/manufacturing company that offers Advanced machining/assembly/engineering services, as well as innovative products for the heavy duty engine cooling markets.

We are looking to get a new business card designed that is clean and modern looking, but still fits the wide range of technical/skilled work we do.

- We hope to use this design as the base for other design work in new Presentations, web, and print work.

Industry/Entity Type

Engineering

Contact Information for Business Card

Our preferred color of blue is (RGB) 22/71/159 but can vary slightly from that color. Our content will be our Logo and full company name (Vantrell Forge Works, Inc.), company address, name, job title, phone number with extension, cell number, fax number, website, and email address on the cards.
We'd like the full company name next to the logo, but we are open to other interpretations of that layout.
Preferably, we would like the back side to be clean with just our logo, and the front to contain all of the contact information.

Colors
2f74b4
0355a3
85abd2

Requirements
Must have
• - Logo, company name, needed content - We are open to interpretation beyond that.
• - Standard size business card.
• - Horizontal orientation.
• - Enough space for lengthy names / job titles (for example, a job title could read "Directory of Human Resources" or "V.P. of Governmental Affairs"). We need this to look clean, whether the title be short (CEO) or long (as described above).

```html
<!DOCTYPE html>
<html lang="en">
<head>
<meta charset="utf-8">
<title>Vantrell Forge Works, Inc. – Business Card</title>
<link rel="stylesheet" href="https://fonts.googleapis.com/css2?family=Roboto:wght@400;500;700;900&family=Roboto+Condensed:wght@700&display=swap">
<style>
  :root {
    --brand-blue: #0f52a0;
    --ink: #1a1a1a;
    --ink-soft: #555555;
    --tagline-grey: #7a7a7a;
    --paper: #f2f2f2;
    --backdrop: #2a2a2a;
    --white: #ffffff;
  }
  * { margin: 0; padding: 0; box-sizing: border-box; }
  html, body {
    width: 1200px; height: 960px; overflow: hidden;
    background: var(--backdrop);
    font-family: "Roboto", Arial, sans-serif;
  }
  .canvas { position: relative; width: 1200px; height: 960px; }

  .card { position: absolute; width: 600px; height: 343px; overflow: hidden; }
  .card--front { left: 314px; top: 113px; background: var(--paper); }
  .card--back  { left: 311px; top: 472px; background: var(--brand-blue); }

  .corner { position: absolute; }
  .corner--top-left { left: 0; top: 0; }
  .corner--bottom-right { right: 0; bottom: 0; }

  .front-mark { position: absolute; right: 44px; top: 46px; text-align: left; }
  .front-mark__name {
    font-weight: 900; font-size: 50px; line-height: 1;
    color: var(--brand-blue); letter-spacing: 1px;
  }
  .front-mark__tagline {
    margin-top: 6px; font-weight: 700; font-size: 13px;
    color: var(--tagline-grey); letter-spacing: 0.3px;
  }

  .contact { position: absolute; left: 45px; top: 178px; }
  .contact__name {
    font-family: "Roboto Condensed", "Arial Narrow", sans-serif;
    font-weight: 700; font-size: 23px; color: var(--brand-blue); line-height: 1;
  }
  .contact__title { margin-top: 5px; font-size: 14px; color: var(--ink); }
  .contact__details { display: flex; margin-top: 14px; }
  .contact__list { list-style: none; }
  .contact__item {
    display: flex; align-items: center; height: 19px;
    font-size: 14px; color: var(--ink-soft);
  }
  .contact__icon { width: 13px; height: 13px; margin-right: 9px; fill: var(--brand-blue); }
  .contact__divider {
    width: 1px; height: 31px; background: var(--ink-soft);
    margin: 40px 23px 0 23px;
  }
  .contact__address { margin-top: 38px; font-size: 14px; line-height: 19px; color: var(--ink-soft); }

  .back-lockup {
    position: absolute; left: 107px; top: 128px;
    display: flex; align-items: flex-start; gap: 16px;
  }
  .back-mark__name {
    font-weight: 900; font-size: 56px; line-height: 1;
    color: var(--white); letter-spacing: 1px;
  }
  .back-mark__tagline {
    margin-top: 8px; font-weight: 700; font-size: 14px;
    color: var(--white); letter-spacing: 0.3px;
  }
  .back-company {
    margin-top: 4px; font-weight: 900; font-size: 17px; line-height: 19px;
    color: var(--white); text-transform: uppercase;
  }
  .back-company__suffix { font-size: 9px; }
</style>
</head>
<body>
<main class="canvas">

  <section class="card card--front" aria-label="Business card front">
    <svg class="corner corner--top-left" width="92" height="92" viewBox="0 0 92 92"><polygon points="0,0 92,0 0,92" fill="var(--brand-blue)"/></svg>
    <svg class="corner corner--bottom-right" width="92" height="92" viewBox="0 0 92 92"><polygon points="92,0 92,92 0,92" fill="var(--brand-blue)"/></svg>

    <div class="front-mark">
      <div class="front-mark__name">VANTRELL</div>
      <div class="front-mark__tagline">BUILT TO ENDURE</div>
    </div>

    <div class="contact">
      <h1 class="contact__name">DALE HARWICK</h1>
      <p class="contact__title">V.P. of Governmental Affairs</p>
      <div class="contact__details">
        <ul class="contact__list">
          <li class="contact__item">
            <svg class="contact__icon" viewBox="0 0 16 16"><path d="M3.6 1l2.6 2.6-1.5 2.2c.9 1.9 2.6 3.6 4.5 4.5l2.2-1.5L14 11.4 12.4 15C6.2 14.6 1.4 9.8 1 3.6z"/></svg>555 214 7730
          </li>
          <li class="contact__item">
            <svg class="contact__icon" viewBox="0 0 16 16"><path d="M4 0h8a1 1 0 0 1 1 1v14a1 1 0 0 1-1 1H4a1 1 0 0 1-1-1V1a1 1 0 0 1 1-1zm1 2v10h6V2zm3 11a1 1 0 1 0 0 2 1 1 0 0 0 0-2z"/></svg>555 382 0196
          </li>
          <li class="contact__item">
            <svg class="contact__icon" viewBox="0 0 16 16"><path d="M1 3h14v10H1zm1.5 1.5v.3L8 8.6l5.5-3.8v-.3zm0 2.1v4.9h11V6.6L8 10.4z"/></svg>dale@vantrell.com
          </li>
          <li class="contact__item">
            <svg class="contact__icon" viewBox="0 0 16 16"><circle cx="8" cy="8" r="7"/><path d="M3 6c2 0 3 1 3 3s2 2 2 4M10 2c0 2 1 3 3 3" stroke="var(--paper)" stroke-width="1.3" fill="none"/></svg>www.vantrell.com
          </li>
        </ul>
        <span class="contact__divider" aria-hidden="true"></span>
        <address class="contact__address" style="font-style:normal">
          4120 Cedar Ridge Road<br>Fairbanks, Alaska 99701
        </address>
      </div>
    </div>
  </section>

  <section class="card card--back" aria-label="Business card back">
    <div class="back-lockup">
      <div class="back-mark">
        <div class="back-mark__name">VANTRELL</div>
        <div class="back-mark__tagline">BUILT TO ENDURE</div>
      </div>
      <div class="back-company">
        Vantrell<br>Forge<br>Works <span class="back-company__suffix">Inc</span>
      </div>
    </div>
  </section>

</main>
</body>
</html>
```